Veltrane Group Business Card Design

The CEO is looking for a new trendy look for his business card.
You can stay with current branding or come up with something new/creative. It can be 3D, including Medical Office buildings. You can use our logo in a variety of colors. Please include name, title, company name, company website, email address, cell number

Target Market(s)

Real Estate Development and Construction

Industry/Entity Type

Health care real estate

Contact Information for Business Card

Rohesh Kamdar, CEO M-604.781.2249 E-roheshkamdar@veltrane.com Address:4180 Lindqvist Ave, Tampa, FL 33482 www.veltrane.com

Font styles to use
Other font styles liked:
• Be creative

Requirements
Must have
• Creative, trendy look
Nice to have
• Please go to our website to get a feel- www. veltrane.com
Should not have
• small fonts

```html
<!DOCTYPE html>
<html lang="en">
<head>
<meta charset="utf-8">
<title>Veltrane Group Business Card</title>
<link rel="stylesheet" href="https://fonts.googleapis.com/css2?family=Montserrat:wght@400;700;800&display=swap">
<style>
  :root {
    --bg: #e9e6e1;
    --card-light: #ffffff;
    --card-dark: #171717;
    --ink: #111111;
    --ink-soft: #1c1c1c;
    --white: #ffffff;
    --shadow: 0 10px 24px rgba(0,0,0,0.28);
  }
  * { margin: 0; padding: 0; box-sizing: border-box; }
  html, body {
    width: 900px; height: 1200px; overflow: hidden;
    background: var(--bg);
    font-family: "Montserrat", Arial, sans-serif;
    color: var(--ink);
  }
  .stage { position: relative; width: 900px; height: 1200px; }

  .card { position: absolute; box-shadow: var(--shadow); overflow: hidden; }
  .card--front { left: 80px; top: 131px; width: 742px; height: 440px; background: var(--card-light); }
  .card--back { left: 78px; top: 638px; width: 744px; height: 440px; background: var(--card-dark); }

  .stripes { position: absolute; inset: 0; }

  .person { position: absolute; left: 35px; top: 57px; }
  .person__name { font-weight: 700; font-size: 26px; letter-spacing: 0.2px; line-height: 1.1; }
  .person__title { font-weight: 400; font-size: 16px; margin-top: 6px; }

  .address { position: absolute; left: 35px; top: 265px; font-size: 16px; line-height: 22px; }

  .contacts { position: absolute; left: 35px; top: 324px; list-style: none; font-size: 16px; }
  .contacts li { display: flex; align-items: center; height: 28px; }
  .contacts svg { width: 16px; height: 16px; margin-right: 12px; fill: var(--ink); }

  .wordmark {
    position: absolute; font-weight: 800; line-height: 0.9;
    text-align: right; letter-spacing: -1px;
  }
  .wordmark span { display: block; }
  .wordmark--front { right: 42px; top: 165px; color: var(--ink); }
  .wordmark--front .wordmark__name { font-size: 64px; }
  .wordmark--front .wordmark__group { font-size: 34px; margin-top: 4px; }

  .wordmark--back { left: 50%; top: 130px; transform: translateX(-50%); color: var(--white); }
  .wordmark--back .wordmark__name { font-size: 96px; }
  .wordmark--back .wordmark__group { font-size: 50px; margin-top: 6px; }
</style>
</head>
<body>
<main class="stage">

  <section class="card card--front" aria-label="Business card front">
    <svg class="stripes" width="742" height="440" viewBox="0 0 742 440" aria-hidden="true">
      <polygon points="525,0 713,0 655,160 468,160" fill="var(--ink-soft)"/>
      <polygon points="413,319 585,319 537,440 357,440" fill="var(--ink-soft)"/>
    </svg>

    <div class="person">
      <p class="person__name">Rohesh Kamdar</p>
      <p class="person__title">CEO</p>
    </div>

    <p class="address">4180 Lindqvist Ave,<br>Tampa, FL 33482</p>

    <ul class="contacts">
      <li>
        <svg viewBox="0 0 24 24" aria-hidden="true"><path d="M6.6 10.8a15.1 15.1 0 0 0 6.6 6.6l2.2-2.2c.3-.3.7-.4 1-.2 1.1.4 2.3.6 3.6.6.6 0 1 .4 1 1V20c0 .6-.4 1-1 1A17 17 0 0 1 3 4c0-.6.4-1 1-1h3.5c.6 0 1 .4 1 1 0 1.3.2 2.5.6 3.6.1.3 0 .7-.2 1z"/></svg>
        <span>604.781.2249</span>
      </li>
      <li>
        <svg viewBox="0 0 24 24" aria-hidden="true"><path d="M3 5h18v2l-9 6-9-6z M3 9l9 6 9-6v10H3z"/></svg>
        <span>roheshkamdar@veltrane.com</span>
      </li>
      <li>
        <svg viewBox="0 0 24 24" aria-hidden="true"><path d="M12 2a10 10 0 1 0 0 20 10 10 0 0 0 0-20zm6.9 6h-3a15 15 0 0 0-1.3-4A8 8 0 0 1 18.9 8zM12 4c.8 1.2 1.5 2.5 1.9 4h-3.8c.4-1.5 1.1-2.8 1.9-4zM4.3 14a8 8 0 0 1 0-4h3.4a16 16 0 0 0 0 4zm.8 2h3a15 15 0 0 0 1.3 4A8 8 0 0 1 5.1 16zm3-8h-3a8 8 0 0 1 4.3-4 15 15 0 0 0-1.3 4zM12 20c-.8-1.2-1.5-2.5-1.9-4h3.8c-.4 1.5-1.1 2.8-1.9 4zm2.3-6H9.7a14 14 0 0 1 0-4h4.6a14 14 0 0 1 0 4zm.3 6a15 15 0 0 0 1.3-4h3a8 8 0 0 1-4.3 4zm1.7-6a16 16 0 0 0 0-4h3.4a8 8 0 0 1 0 4z"/></svg>
        <span>www.veltrane.com</span>
      </li>
    </ul>

    <p class="wordmark wordmark--front">
      <span class="wordmark__name">Veltrane</span>
      <span class="wordmark__group">Group</span>
    </p>
  </section>

  <section class="card card--back" aria-label="Business card back">
    <p class="wordmark wordmark--back">
      <span class="wordmark__name">Veltrane</span>
      <span class="wordmark__group">Group</span>
    </p>
  </section>

</main>
</body>
</html>
```